Real estate broker business card

Want a modern celan but effective business card for my residential and commercial real estate business. I want the back of the card to advertise my services and to capture business. I have attached the back of my current business card fore ideas
Updates

Logos, photo and text updates added! Added Saturday, September 3, 2016

Project Deadline Extended Reason: LOGOS, PHOTOS AND TEST JUST UPLOADED! I'M READY TO PICK A DESIGN! THANK YOU! Added Saturday, September 3, 2016

Target Market(s)

home buyers and seller. commercial buyers and sellers

Industry/Entity Type

Real Estate

Contact Information for Business Card

must have my contact information and my photo

Requirements
Must have
• Carla Ventrino
• Owner & Qualifying Broker
• Ventrino Real Estate Services
• 505.718.2094
• carla@ventrinohomes.example
• www.ventrinohomes.example
Nice to have
• metallic
• Business capture text: " Don't buy or lease property without someone looking out for your best interests. I will represent you on your home or investment purchase for FREE!"
• "Home owners, call today to receive a FREE market analysis for your homes value!

```html
<!DOCTYPE html>
<html lang="en">
<head>
<meta charset="utf-8">
<title>Ventrino Real Estate Services – Business Card</title>
<link href="https://fonts.googleapis.com/css2?family=Cinzel:wght@500&family=Source+Sans+3:wght@400&display=swap" rel="stylesheet">
<style>
  :root {
    --teal: #1a8796;
    --teal-light: #22a0b0;
    --teal-dark: #0f6570;
    --white: #ffffff;
    --ink-grey: #5b6366;
    --backdrop: #ececec;
    --photo-dark: #2e3b2c;
    --photo-mid: #5b6b4e;
    --frame: #2a3032;
  }
  * { box-sizing: border-box; margin: 0; padding: 0; }
  html, body { width: 1200px; height: 950px; overflow: hidden; }
  body {
    background: var(--backdrop);
    font-family: "Source Sans 3", "Helvetica Neue", Arial, sans-serif;
    position: relative;
  }
  .card {
    position: absolute;
    left: 250px;
    width: 700px;
    height: 400px;
    overflow: hidden;
    border-radius: 4px;
    box-shadow: 0 6px 18px rgba(0,0,0,0.18);
  }

  /* Back side */
  .card--back {
    top: 50px;
    background: radial-gradient(ellipse at 50% 40%, var(--teal-light) 0%, var(--teal) 55%, var(--teal-dark) 100%);
    color: var(--white);
    text-align: center;
  }
  .back-brand {
    position: absolute;
    top: 110px;
    left: 0; right: 0;
    display: flex;
    align-items: center;
    justify-content: center;
    gap: 14px;
  }
  .back-brand__dot {
    width: 18px; height: 18px;
    border-radius: 50%;
    background: var(--white);
  }
  .back-brand__name {
    font-family: "Cinzel", Georgia, serif;
    font-weight: 500;
    font-size: 30px;
    letter-spacing: 3px;
    color: var(--white);
  }
  .back-offer {
    position: absolute;
    top: 250px;
    left: 0; right: 0;
    font-size: 20px;
    line-height: 1.3;
  }

  /* Front side */
  .card--front {
    top: 500px;
    background: var(--white);
  }
  .front-band {
    position: absolute;
    inset: 0;
    width: 700px;
    height: 400px;
  }
  .front-photo {
    position: absolute;
    left: 440px;
    top: 22px;
    width: 205px;
    height: 228px;
    border-radius: 14px;
    border: 5px solid var(--frame);
    background: radial-gradient(ellipse at 55% 55%, var(--photo-mid) 0%, var(--photo-dark) 80%);
  }
  .front-brand {
    position: absolute;
    left: 40px;
    top: 110px;
    display: flex;
    align-items: center;
    gap: 12px;
    color: var(--teal);
    font-family: "Cinzel", Georgia, serif;
    font-weight: 500;
  }
  .front-brand__dot {
    width: 16px; height: 16px;
    border-radius: 50%;
    background: var(--teal);
  }
  .front-brand__name { font-size: 34px; letter-spacing: 1px; line-height: 1; }
  .front-brand__sub { display: block; font-size: 12px; letter-spacing: 3px; margin-top: 4px; }
  .front-person {
    position: absolute;
    right: 40px;
    top: 262px;
    text-align: right;
    color: var(--white);
  }
  .front-person__name {
    font-family: "Cinzel", Georgia, serif;
    font-weight: 500;
    font-size: 24px;
    letter-spacing: 1px;
  }
  .front-person__title { font-size: 16px; margin-top: 4px; }
  .front-contact {
    position: absolute;
    left: 40px;
    top: 282px;
    list-style: none;
    color: var(--white);
    font-size: 16px;
  }
  .front-contact li {
    display: flex;
    align-items: center;
    gap: 8px;
    height: 24px;
  }
  .front-contact svg { width: 14px; height: 14px; fill: var(--white); }
</style>
</head>
<body>

  <section class="card card--back" aria-label="Card back">
    <div class="back-brand">
      <span class="back-brand__dot"></span>
      <span class="back-brand__name">VENTRINO</span>
    </div>
    <p class="back-offer">Home owners, call today to receive a FREE<br>market analysis for your homes value!</p>
  </section>

  <section class="card card--front" aria-label="Card front">
    <svg class="front-band" viewBox="0 0 700 400" aria-hidden="true">
      <defs>
        <linearGradient id="bandFill" x1="0" y1="0" x2="1" y2="0">
          <stop offset="0" stop-color="#157d8b"/>
          <stop offset="0.6" stop-color="#22a0b0"/>
          <stop offset="1" stop-color="#17828f"/>
        </linearGradient>
      </defs>
      <polygon points="0,238 700,120 700,400 0,400" fill="url(#bandFill)"/>
    </svg>

    <div class="front-photo" role="img" aria-label="Portrait photo of Carla Ventrino"></div>

    <div class="front-brand">
      <span class="front-brand__dot"></span>
      <span>
        <span class="front-brand__name">VENTRINO</span>
        <span class="front-brand__sub">REAL ESTATE SERVICES</span>
      </span>
    </div>

    <div class="front-person">
      <p class="front-person__name">CARLA VENTRINO</p>
      <p class="front-person__title">Owner &amp; Qualifying Broker , Ventrino Real Estate Services</p>
    </div>

    <ul class="front-contact">
      <li>
        <svg viewBox="0 0 16 16" aria-hidden="true"><path d="M3.5 1 6 4 4.6 5.8c.9 2 2.6 3.7 4.6 4.6L11 9l3 2.5-1.6 2.8C7 14 2 9 1.7 3.6Z"/></svg>
        505.718.2094
      </li>
      <li>
        <svg viewBox="0 0 16 16" aria-hidden="true"><path d="M1 3h14v10H1Zm1.5 1.2L8 8.6l5.5-4.4Z"/></svg>
        carla@ventrinohomes.example
      </li>
      <li>
        <svg viewBox="0 0 16 16" aria-hidden="true"><circle cx="8" cy="8" r="6.5" fill="none" stroke="#fff" stroke-width="1.6"/><path d="M1.5 8h13M8 1.5c-3 3.5-3 9.5 0 13M8 1.5c3 3.5 3 9.5 0 13" fill="none" stroke="#fff" stroke-width="1.2"/></svg>
        www.ventrinohomes.example
      </li>
    </ul>
  </section>

</body>
</html>
```